Upscale business cards needed for Board of Directors

We need professional business cards created for members of our family business Board of Directors. We would like these relatively simple and straightforward, but also with a unique element to set them apart. Probably stick with neutral and simple colors - white, grey etc. We need space for the traditional elements, including name, title, address, email/phone number. And we will be creating several from this template so it needs to be template that is easy to switch information in and out of.
Business
See description

```html
<!DOCTYPE html>
<html lang="en">
<head>
<meta charset="utf-8">
<title>Harborline Holdings – Business Card</title>
<link href="https://fonts.googleapis.com/css2?family=Lato:wght@400;700;900&display=swap" rel="stylesheet">
<style>
  :root {
    --gold: #b19d72;
    --ink: #111111;
    --paper: #ffffff;
    --stage: #d9d8d4;
    --muted: #2a2a2a;
  }
  html, body { margin: 0; padding: 0; overflow: hidden; }
  body {
    width: 1200px; height: 900px;
    background: var(--stage);
    position: relative;
    font-family: "Lato", sans-serif;
  }
  .card {
    position: absolute;
    width: 560px; height: 320px;
    box-shadow: 0 10px 30px rgba(0,0,0,.18);
    overflow: hidden;
  }
  /* Back side */
  .card--back {
    left: 580px; top: 90px;
    background: var(--gold);
  }
  .card--back .brand { position: absolute; left: 0; right: 0; top: 110px; text-align: center; }
  .card--back .web {
    position: absolute; left: 0; right: 0; top: 250px;
    text-align: center; color: var(--paper);
    font-size: 15px; letter-spacing: 2px;
  }
  .brand__name, .brand__sub {
    display: block; color: var(--ink); font-weight: 900; line-height: 1;
  }
  .brand__name { font-size: 40px; letter-spacing: 1px; }
  .brand__sub { font-size: 20px; letter-spacing: 12px; margin-top: 6px; }

  /* Front side */
  .card--front {
    left: 60px; top: 490px;
    background: var(--paper);
  }
  .card--front .brand { position: absolute; left: 40px; top: 42px; }
  .card--front .brand__name { font-size: 34px; }
  .card--front .brand__sub { font-size: 17px; letter-spacing: 10px; }
  .divider {
    position: absolute; left: 40px; width: 380px; top: 134px;
    height: 1px; background: var(--gold);
  }
  .contact {
    position: absolute; left: 40px; top: 152px;
    margin: 0; padding: 0; list-style: none;
    font-size: 13px; color: var(--muted);
  }
  .contact li { display: flex; align-items: center; gap: 8px; height: 20px; }
  .contact svg { width: 11px; height: 11px; fill: var(--gold); }
  .person {
    position: absolute; right: 40px; top: 160px; text-align: right;
  }
  .person__name {
    font-size: 24px; color: var(--ink); margin: 0;
    padding-bottom: 3px; border-bottom: 1px solid var(--gold);
  }
  .person__title { font-size: 15px; color: var(--gold); margin: 3px 0 10px; }
  .person__address { font-size: 14px; color: var(--muted); line-height: 1.3; margin: 0; }
  .footer { position: absolute; left: 0; bottom: 0; width: 560px; height: 44px; }
  .footer__web {
    position: absolute; right: 40px; bottom: 12px;
    color: var(--paper); font-size: 15px; letter-spacing: 1.5px;
  }
</style>
</head>
<body>
  <section class="card card--back">
    <div class="brand">
      <span class="brand__name">HARBORLINE</span>
      <span class="brand__sub">HOLDINGS</span>
    </div>
    <div class="web">www.harborline.com</div>
  </section>

  <section class="card card--front">
    <div class="brand">
      <span class="brand__name">HARBORLINE</span>
      <span class="brand__sub">HOLDINGS</span>
    </div>
    <div class="divider"></div>
    <ul class="contact">
      <li><svg viewBox="0 0 12 12"><path d="M2 1h2l1 3-1.3 1a6 6 0 0 0 3.3 3.3L8 7l3 1v2c0 .6-.4 1-1 1A9 9 0 0 1 1 2c0-.6.4-1 1-1z"/></svg>512 555 0142</li>
      <li><svg viewBox="0 0 12 12"><rect x="3" y="1" width="6" height="3"/><rect x="1" y="4.5" width="10" height="4.5" rx="1"/><rect x="3" y="8" width="6" height="3"/></svg>512 555 0143</li>
      <li><svg viewBox="0 0 12 12"><path d="M1 2.5h10v7H1z M1 2.5l5 4 5-4" stroke="#fff" stroke-width=".8"/></svg>info@harborline.com</li>
    </ul>
    <div class="person">
      <p class="person__name">Daniel Whitford</p>
      <p class="person__title">Director</p>
      <p class="person__address">4100 Cedar Lane<br>Marlow TX 78010</p>
    </div>
    <svg class="footer" viewBox="0 0 560 44" aria-hidden="true">
      <rect x="0" y="30" width="240" height="14" fill="var(--ink)"/>
      <path d="M230 44 C236 20 244 6 270 6 L560 6 L560 44 Z" fill="var(--gold)"/>
      <path d="M226 44 L230 44 C236 20 244 6 270 6 L272 6 C246 8 240 22 234 44 Z" fill="var(--paper)"/>
    </svg>
    <span class="footer__web">www.harborline.com</span>
  </section>
</body>
</html>
```